Easy Marinade Labels for Butchery Store

Need a set of labels designed for a Butchery Shop. They will sit in the top left corner of the packets as a triangle (7cm each side). Easy because the only major requirement is the label name and some small text saying "Please ask in store to see spec sheet for ingredients". Extra points for finding a fun way to incorporate the logo and/or images of food (garlic bulbs, chilli, spices ect) to enhance the label. List of Marinade Names below: GarlicPepper Mint & RosemarySatayBBQChilli Plum & GingerSundried Tomato & BasilBuffaloHoney SoyHoi-SinPer PeriSpicy CajunTeriyakiBlack Bean Ive also attached the logo and an example of how the label might sit on a packet of meat. Thanks

Target Market(s)

Butchery Deli Shop Customers

Industry/Entity Type

Food Store

Font styles to use
Serif
Sans Serif
Decorative
Other font styles liked:
• Fun font that isn't a generic Quellbrix Font?

Colors

Designer to choose colors to be used in the design.

Requirements
Must have
• Product Name
• Small text saying "Please ask in store to see spec sheet for ingredients"
Nice to have
• Photos of ingredients that would match that type of marinade - Chilli, Garlic, Spices.
• Fenly Oak Logo - not essential if it doesn't look good on the label / doesn't fit.

```html
<!DOCTYPE html>
<html lang="en">
<head>
<meta charset="UTF-8">
<title>Peri Peri Marinade Label</title>
<link href="https://fonts.googleapis.com/css2?family=Londrina+Solid:wght@400&family=Open+Sans:wght@800&display=swap" rel="stylesheet">
<style>
  :root {
    --page: #ffffff;
    --frame-yellow: #f2f215;
    --label-text: #ffffff;
    --onion-violet: #c98fd6;
    --beet-purple: #7a1f4a;
    --chilli-red: #c8231c;
    --pepper-orange: #d9541c;
    --lemon-yellow: #f0c21e;
    --shade: rgba(20, 10, 10, 0.75);
  }
  html, body {
    margin: 0;
    padding: 0;
    width: 1200px;
    height: 900px;
    overflow: hidden;
    background: var(--page);
  }
  .canvas {
    position: relative;
    width: 1200px;
    height: 900px;
    background: var(--page);
  }
  .label-shape {
    position: absolute;
    left: 0;
    top: 0;
    width: 1200px;
    height: 900px;
  }
  .marinade-name {
    position: absolute;
    left: 520px;
    top: 364px;
    width: 200px;
    margin: 0;
    text-align: center;
    font-family: "Londrina Solid", "Impact", "Arial Narrow", sans-serif;
    font-weight: 400;
    font-size: 80px;
    line-height: 89px;
    color: var(--label-text);
    letter-spacing: 1px;
  }
  .ingredients-note {
    position: absolute;
    left: 142px;
    top: 601px;
    width: 958px;
    margin: 0;
    text-align: center;
    font-family: "Open Sans", sans-serif;
    font-weight: 800;
    font-size: 22px;
    line-height: 1;
    letter-spacing: 1.8px;
    color: var(--label-text);
    white-space: nowrap;
  }
</style>
</head>
<body>
<main class="canvas">
  <svg class="label-shape" viewBox="0 0 1200 900" xmlns="http://www.w3.org/2000/svg">
    <defs>
      <clipPath id="label-clip">
        <polygon points="620,176 1091,642 151,642"/>
      </clipPath>
      <linearGradient id="produce-tones" x1="0" y1="0" x2="1" y2="0.35">
        <stop offset="0" stop-color="var(--chilli-red)"/>
        <stop offset="0.3" stop-color="var(--pepper-orange)"/>
        <stop offset="0.45" stop-color="var(--chilli-red)"/>
        <stop offset="0.62" stop-color="var(--beet-purple)"/>
        <stop offset="0.75" stop-color="var(--lemon-yellow)"/>
        <stop offset="1" stop-color="var(--lemon-yellow)"/>
      </linearGradient>
      <radialGradient id="onion-glow" cx="0.53" cy="0.32" r="0.22">
        <stop offset="0" stop-color="var(--onion-violet)"/>
        <stop offset="1" stop-color="var(--onion-violet)" stop-opacity="0"/>
      </radialGradient>
      <linearGradient id="base-shade" x1="0" y1="0" x2="0" y2="1">
        <stop offset="0" stop-color="var(--shade)" stop-opacity="0"/>
        <stop offset="1" stop-color="var(--shade)"/>
      </linearGradient>
    </defs>
    <g class="ingredient-photo" clip-path="url(#label-clip)" role="img" aria-label="Photo of red chillies, peppers, red onion and lemon wedges">
      <polygon points="620,176 1091,642 151,642" fill="url(#produce-tones)"/>
      <polygon points="620,176 1091,642 151,642" fill="url(#onion-glow)"/>
      <rect x="151" y="575" width="940" height="67" fill="url(#base-shade)"/>
    </g>
    <polygon class="label-frame" points="620,174 1096,645 146,645" fill="none" stroke="var(--frame-yellow)" stroke-width="6" stroke-linejoin="miter"/>
  </svg>
  <h1 class="marinade-name">PERI<br>PERI</h1>
  <p class="ingredients-note">PLEASE ASK IN STORE TO SEE SPEC SHEET FOR INGREDIENTS</p>
</main>
</body>
</html>
```